Golf Brochure + Business Card Design Project – Kestrel Fitness.

Task Description

We are looking for a premium tri-fold brochure (8.5x11 letter, folded) plus a new business card design for Kestrel Fitness. Both need to look polished, elegant, and professional — something that would feel at home in a golf club environment.

Brochure Scope:
• Tri-fold brochure promoting our new golf-specific services
• Incorporate brand colors: deep hunter green, cream, and gold accents
• Clean, modern typography (professional, not playful)
• Layout will follow the copy provided (final copy attached, no rewriting needed)
• Imagery: mature golfers (50+), golf lifestyle shots, no generic stocky images
• Include QR code placement linking to booking page
• Deliverables: print-ready PDF with bleed/crop (CMYK), high-res PDF (digital), and source file (InDesign or Illustrator)

Business Card Scope:
• Front + back design
• Consistent with brand colors and fonts
• Space for name, title, phone, email, and website
• Deliverables: print-ready PDF with bleed/crop (CMYK) + source file (AI or InDesign)
• If possible, provide editable template for future staff cards

Timeline:
• First draft within 5–7 days
• 2 rounds of revisions included

Budget:
$300 USD (total for both brochure + business card)

I’ll provide finalized copy if you accept the project.
Project description (paste this whole block in that box)

We need a premium tri-fold brochure (8.5”×11” letter, folded) and a new business card design for Kestrel Fitness. This will be presented to golf course managers and members, so the look must be elegant, restrained, and country-club-classy.

Scope — Brochure
• Format: Tri-fold, 8.5”×11”. Please set 0.125” bleed on all sides and keep critical text ≥0.125–0.25” inside the trim.
• Purpose: Promote Kestrel Fitness’ golf-specific services for adults 50+.
• Copy: We will provide finalized copy in a Word doc after acceptance. No rewriting needed — please focus on layout and polish.
• Imagery (required):
• Golf-first images (ball on tee/green, mature golfers mid-swing, and golf course landscapes at golden hour).
• 1–2 real Kestrel Fitness gym photos on inside panels (trainer with client doing golf-relevant movement: stretch, rotation, balance).
• Visual style: Premium, quiet, lots of white/negative space, balanced grids; no clutter.
• Brand colors (required): Hunter Green #0C2E1F, Gold #CBA135, Cream #F5F2EB. Convert for CMYK print while preserving the look.
• Typography: Clean, legible serif + sans pairing (e.g., modern serif for headlines, humanist/neo-grotesk sans for body). You may propose suitable professional fonts; avoid playful/novelty fonts.
• Elements to include:
• Our logo (we will upload).
• QR code placement to booking page (we will supply the URL / QR asset).
• Simple icon treatment for the three complimentary options (Strength & Mobility, Stretch Therapy, Vitrascan + Assessment).
• Deliverables:
• Print-ready PDF (CMYK, with bleed & crop marks, PDF/X-1a or PDF/X-4)
• High-res digital PDF (no bleed)
• Source file (InDesign or Illustrator) + packaged fonts/links or outlined type as appropriate.

Scope — Business Card
• Size: 3.5”×2” (US standard) with 0.125” bleed; keep text ≥0.125” from trim.
• Front/back design; consistent with brochure branding.
• Fields: Name, Title, Phone, Email, Website, Address; optional small QR on back.
• Deliverables: Print-ready PDF (CMYK, bleed & crops) + Source file (AI/INDD). Provide an editable template for staff names.

Process & Timing
• Initial concept for brochure + card within 5–7 days of acceptance.
• 2 rounds of revisions included.
• Please start with a clean layout concept using placeholder images/text blocks; we’ll drop in final copy/assets immediately after acceptance.

Stock & Licensing
• You may propose stock images that fit the brief (we’re fine approving Pixelgrove or equivalent). Please note any license fees separately if needed.

Usage Rights
• We require full usage rights to the final designs for print & digital.

Target Market(s)

Golfers 50+ in Victoria, BC: quality-oriented, health-conscious, want to play longer, stronger, and pain-free. Country-club aesthetic; expect polished, professional materials.

Industry/Entity Type

Health & Fitness — Golf Performance / Longevity Studio

Font styles to use
Serif
Sans Serif

Requirements
Must have
• • Golf-first imagery + 1–2 real Kestrel Fitness photos inside. • Brand colors: #0C2E1F (Hunter Green), #CBA135 (Gold), #F5F2EB (Cream). • Premium, restrained layout; ample negative space; no clutter. • Clean professional serif + sans type pairing; highly legible. • Space for logo and QR code (booking). • Correct print specs (bleed, crops, CMYK). • Deliverables: print-ready PDFs (brochure + card), digital PDF, source files.
Nice to have
• • Subtle texture or grain in backgrounds (very light) to add sophistication. • A second brochure cover variation (ball on tee vs. course landscape) at concept stage.
Should not have
• • Cheesy/posed “stocky” groups; overly young models; beer/alcohol imagery. • Over-saturated greens/blues; gimmicky gradients or clip art. • Generic fitness/bodybuilding shots unrelated to golf performance.

```html
<!DOCTYPE html>
<html lang="en">
<head>
<meta charset="utf-8">
<title>Kestrel Fitness – Business Card</title>
<link rel="stylesheet" href="https://fonts.googleapis.com/css2?family=Jost:wght@300;400;500;600;700&family=Barlow:wght@400;500&display=swap">
<style>
  :root {
    --hunter: #0c3a26;
    --hunter-deep: #0a2e1f;
    --hunter-mid: #1b4a33;
    --gold: #cba135;
    --cream: #f1ece6;
    --cream-shade: #e6e0da;
    --ink: #0e2a1e;
    --ink-soft: #2b2b2b;
    --stage: #cbccce;
  }
  * { margin: 0; padding: 0; box-sizing: border-box; }
  html, body { width: 1011px; height: 1200px; overflow: hidden; background: var(--stage); }
  .canvas { position: relative; width: 1011px; height: 1200px; }

  .card {
    position: absolute; left: 70px; width: 871px; height: 497px; overflow: hidden;
    box-shadow: 0 6px 24px rgba(0,0,0,0.12);
  }
  .card--front { top: 75px; background: var(--hunter-deep); }
  .card--back { top: 628px; background: var(--cream); }

  .front-scene {
    position: absolute; inset: 0;
    background:
      radial-gradient(ellipse at 72% 20%, rgba(40,70,50,0.55), transparent 45%),
      radial-gradient(ellipse at 20% 40%, rgba(30,60,40,0.5), transparent 50%),
      linear-gradient(180deg, #1a3a2a 0%, #123d28 55%, #163f2b 100%);
  }
  .gold-band {
    position: absolute; left: 0; right: 0; top: 156px; height: 115px;
    background: linear-gradient(90deg, #c89f32, #d2a838 50%, #c99f30);
  }
  .brand-disc {
    position: absolute; left: 283px; top: 57px; width: 306px; height: 306px;
    border-radius: 50%; background: radial-gradient(circle, #0d3f27 0%, #0f3a25 70%, #143f2b 100%);
    display: flex; align-items: center; justify-content: center; text-align: center;
  }
  .brand-name {
    font-family: "Jost", sans-serif; font-weight: 600; color: var(--gold);
    letter-spacing: 0.18em; text-transform: uppercase; line-height: 1.15;
  }
  .brand-disc .brand-name { font-size: 34px; }
  .tagline {
    position: absolute; left: 0; right: 0; top: 396px; text-align: center;
    font-family: "Jost", sans-serif; font-weight: 300; font-size: 41px;
    color: var(--gold); letter-spacing: 0.01em; white-space: nowrap;
  }
  .tagline strong { font-weight: 600; }

  .back-scene {
    position: absolute; inset: 0;
    background:
      radial-gradient(ellipse at 28% 35%, rgba(210,200,192,0.55), transparent 45%),
      radial-gradient(ellipse at 72% 70%, rgba(205,196,188,0.5), transparent 45%),
      linear-gradient(180deg, var(--cream) 0%, var(--cream-shade) 100%);
  }
  .back-mark {
    position: absolute; left: 641px; top: 38px; width: 178px; height: 178px;
    border: 2.5px solid var(--ink); border-radius: 50%;
    display: flex; align-items: center; justify-content: center; text-align: center;
  }
  .back-mark .brand-name { color: var(--ink); font-size: 20px; }

  .holder-name {
    position: absolute; left: 48px; top: 322px;
    font-family: "Jost", sans-serif; font-weight: 500; font-size: 47px;
    color: var(--ink); letter-spacing: 0.01em; white-space: nowrap;
  }
  .holder-role {
    position: absolute; left: 49px; top: 373px;
    font-family: "Barlow", sans-serif; font-weight: 400; font-size: 21px;
    color: var(--ink-soft); letter-spacing: 0.02em;
  }
  .rule {
    position: absolute; left: 49px; top: 419px; width: 772px; height: 4px; background: var(--gold);
  }
  .contact-row {
    position: absolute; left: 49px; top: 442px; width: 773px;
    display: flex; align-items: center; justify-content: space-between;
    font-family: "Barlow", sans-serif; font-size: 17px; color: var(--ink-soft);
  }
  .contact-item { display: flex; align-items: center; gap: 15px; white-space: nowrap; }
  .contact-item svg { width: 15px; height: 15px; fill: var(--ink-soft); }
  .divider { color: var(--ink-soft); }
</style>
</head>
<body>
<main class="canvas">

  <section class="card card--front" aria-label="Card front">
    <div class="front-scene" role="img" aria-label="Golf course landscape with trees, toned in deep green"></div>
    <div class="gold-band"></div>
    <div class="brand-disc">
      <div class="brand-name">Kestrel<br>Fitness</div>
    </div>
    <p class="tagline">STRENGTH • <strong>MOBILITY</strong> • LONGEVITY</p>
  </section>

  <section class="card card--back" aria-label="Card back">
    <div class="back-scene" role="img" aria-label="Faded gym photo of a trainer working with a client"></div>
    <div class="back-mark">
      <div class="brand-name">Kestrel<br>Fitness</div>
    </div>

    <h1 class="holder-name">MAREN-LEE ASHFORD</h1>
    <p class="holder-role">OWNER | KESTREL FITNESS</p>
    <div class="rule"></div>

    <div class="contact-row">
      <span class="contact-item">
        <svg viewBox="0 0 16 16" aria-hidden="true"><rect x="0" y="0" width="16" height="16" rx="2"/><path d="M5 3.5l1.6 2.2-1 1a6 6 0 0 0 3.7 3.7l1-1 2.2 1.6-.9 1.6C7.8 12.8 3.2 8.2 3.4 4.4z" fill="#f1ece6"/></svg>
        250-555-0147
      </span>
      <span class="divider">|</span>
      <span class="contact-item">
        <svg viewBox="0 0 16 12" aria-hidden="true" style="width:17px;height:13px"><path d="M0 1.2A1.2 1.2 0 0 1 1.2 0h13.6A1.2 1.2 0 0 1 16 1.2v.4L8 6.8 0 1.6z"/><path d="M0 3.4l8 5.2 8-5.2v7.4A1.2 1.2 0 0 1 14.8 12H1.2A1.2 1.2 0 0 1 0 10.8z"/></svg>
        maren-lee@kestrelfitness.biz
      </span>
      <span class="divider">|</span>
      <span class="contact-item">
        <svg viewBox="0 0 16 16" aria-hidden="true"><circle cx="8" cy="8" r="8"/><path d="M4 3.5c1.5.5 2 1.8 1.5 3S7 8.5 6.5 10 5 12 4.5 13M10 2.5c-.5 1.5.5 2.5 2 2.8s1.5 2 .5 3.2" stroke="#f1ece6" stroke-width="1.3" fill="none"/></svg>
        kestrelfitnessvictoria.com
      </span>
    </div>
  </section>

</main>
</body>
</html>
```